International Clinical Software Company needs a new business card design

We are looking for a new business card design for our company that has recently expanded into the UK market, making us a multinational company.
After having rebranded our website and produced a new style guide, we are looking for a business card that is creative and attention grabbing, while being consistent with the style and colour scheme used on the new website, www.plumvora.example
We produce care management technology for the aged care market, but the main aspect we aim to communicate is the human element of our software, and the way it assists in providing better care for aged people, and stronger relationships between aged people and the staff that care for them.
Our current business card is a dark green with gold text, which makes the text quite difficult to read, not very aesthetically appealing and the colour scheme looks quite dated.
We would like something fresh and modern, that can still be colourful but doesn't use large blocks of dark colour, and uses the colours within our logo.
Something tying in with the leaves that are used in our logo could work quite nicely, along with the Autumn/Fall colours of soft greens, yellows and reds (also in our existing logo). However also happy to look at fresh, completely out of the box ideas we may not have yet considered.
Target Market(s)
The people that receive this business card work in the aged card or health industry and are either corporate/management level staff or clinical (Registered Nurses, care workers etc.)
Industry/Entity Type
Health Product
Contact Information for Business Card
Company Name - BrindlewayCare
Company locations: Northvale, Eastmere, Southhaven Isles
Staff Details:
Staff name: Derek Mallow
Staff job title: Executive Chairman
Staff email: d.mallow@plumvora.example
Office phone number: 01742 918576
Font styles to use
Other font styles liked:
- Calibri
Requirements
Must have
- Must include the BrindlewayCare brand name in it's current font
- Must include logo (3 leaves in gold circle)
- Must include Business Card Details
Nice to have
- Elements of gold
- White space
- Something autumn themed but not too cliched
Should not have
- No blue - used by a major competitor and we would like to differentiate from them
- Large blocks of dark green colour (the green that appears in our leaves on the logo on our current business card is the background colour and it is far too dark)

```html
<!DOCTYPE html>
<html lang="en">
<head>
<meta charset="utf-8">
<title>BrindlewayCare – Business Card</title>
<link href="https://fonts.googleapis.com/css2?family=Open+Sans:wght@300;400;600&display=swap" rel="stylesheet">
<style>
  :root {
    --stage: #4b5262;
    --card-cream: #fbf6e4;
    --card-white: #ffffff;
    --card-mint: #eef3e8;
    --leaf-blush: rgba(222, 150, 120, 0.5);
    --leaf-peach: rgba(240, 200, 150, 0.3);
    --gold: #b39a2c;
    --gold-icon: #c6a232;
    --tan: #b7a06e;
    --ink: #2a2a2a;
    --muted: #3c3c3c;
  }
  * { margin: 0; padding: 0; box-sizing: border-box; }
  html, body {
    width: 1200px;
    height: 960px;
    overflow: hidden;
  }
  body {
    background: var(--stage);
    display: flex;
    align-items: center;
    justify-content: center;
    font-family: "Open Sans", Calibri, Arial, sans-serif;
  }
  .business-card {
    position: relative;
    width: 1050px;
    height: 600px;
    border-radius: 36px;
    overflow: hidden;
    background:
      radial-gradient(ellipse 520px 260px at 35% 45%, rgba(250, 228, 170, 0.5), transparent 70%),
      radial-gradient(ellipse 300px 200px at 62% 30%, var(--card-mint), transparent 70%),
      linear-gradient(120deg, var(--card-cream) 0%, #fdf9ee 55%, var(--card-white) 100%);
    box-shadow: 0 18px 40px rgba(0, 0, 0, 0.35);
  }
  .leaf-decoration {
    position: absolute;
    left: 130px;
    top: -80px;
    width: 320px;
    height: 320px;
    border-radius: 50%;
    background: radial-gradient(circle at 50% 45%, var(--leaf-blush), var(--leaf-peach) 50%, transparent 72%);
  }
  .card-details {
    position: absolute;
    right: 78px;
    top: 118px;
    display: flex;
    flex-direction: column;
    align-items: flex-end;
    text-align: right;
  }
  .brand {
    display: flex;
    flex-direction: column;
    align-items: flex-end;
    gap: 10px;
  }
  .brand-mark {
    width: 120px;
    height: 120px;
    margin-right: 40px;
  }
  .brand-name {
    font-size: 50px;
    font-weight: 300;
    color: var(--tan);
    line-height: 1;
    letter-spacing: 1px;
  }
  .person-name {
    margin-top: 12px;
    font-size: 34px;
    font-weight: 600;
    color: var(--gold);
    line-height: 1.1;
  }
  .person-title {
    font-size: 24px;
    color: var(--muted);
    margin-top: 2px;
  }
  .contact-list {
    list-style: none;
    margin-top: 22px;
    display: flex;
    flex-direction: column;
    align-items: flex-end;
    gap: 4px;
  }
  .contact-item {
    display: flex;
    align-items: center;
    gap: 14px;
    font-size: 24px;
    color: var(--ink);
    line-height: 1.3;
  }
  .contact-icon {
    width: 28px;
    height: 24px;
    fill: var(--gold-icon);
    flex: none;
  }
  .locations {
    font-size: 24px;
    color: var(--ink);
    line-height: 1.3;
    margin-top: 4px;
    margin-right: 42px;
  }
</style>
</head>
<body>
  <main class="business-card">
    <div class="leaf-decoration" role="img" aria-label="Faded autumn leaf in soft blush and peach tones"></div>

    <section class="card-details">
      <div class="brand">
        <svg class="brand-mark" viewBox="0 0 120 120" aria-hidden="true">
          <circle cx="60" cy="60" r="56" fill="none" stroke="var(--tan)" stroke-width="4"/>
        </svg>
        <span class="brand-name">BrindlewayCare</span>
      </div>

      <h1 class="person-name">Derek Mallow</h1>
      <p class="person-title">Executive Chairman</p>

      <ul class="contact-list">
        <li class="contact-item">
          <span>01742 918576</span>
          <svg class="contact-icon" viewBox="0 0 28 24" aria-hidden="true">
            <path d="M3 7c0-3 5-5 11-5s11 2 11 5v2h-6V7H9v2H3z"/>
            <path d="M6 10h16l3 12H3z"/>
          </svg>
        </li>
        <li class="contact-item">
          <span>d.mallow@plumvora.example</span>
          <svg class="contact-icon" viewBox="0 0 28 24" aria-hidden="true">
            <path d="M2 4h24v16H2z"/>
            <path d="M2 4l12 9 12-9" fill="none" stroke="#fff" stroke-width="2"/>
          </svg>
        </li>
        <li class="contact-item">
          <span>BrindlewayCare</span>
          <svg class="contact-icon" viewBox="0 0 28 24" aria-hidden="true">
            <path d="M14 2L1 13h4v9h7v-6h4v6h7v-9h4z"/>
          </svg>
        </li>
      </ul>
      <p class="locations">Northvale, Eastmere, Southhaven Isles</p>
    </section>
  </main>
</body>
</html>
```